ORV Fashion Design Company Needs a New Web Design, Please Click Me

Designers:

PLEASE NOTE: we only need the web page design, not a fully coded website.

Our brand's name is Orbel Vantra, our signature is print. our style is edgy and chic.

The old website is too messy. here's the address:
www.orvdesign.example.cn

The new website's purpose is to show our brand/design and most importantly, sell products, So it should be a combination of a designer official website and online shopping. I want the whole style to be clean, edgy and pioneer, easy to understand. we need a sophisticated online shopping website.

The reference websites are:
liromapek.example.uk
www.qd-besu.example
talemkorv.example
misolvare.example
pardelunitram.example

Please beat their designs :)

Check out our lasted fashion show to get to know us more.

https://www.videohost.example/watch?v=ZkrpLmWnaYd&spfreload=10

The attachments are our Logo and some 2015 Look Book.
(Please let us know if you want to play with our print in this particular web design, we can send the source file.)
Updates

Designers, we really like the design of helenamardoux.example(we have attached a picture of the website) , Can we get a homepage like that? so the designs you submit will be 3 pages. The first one should be a page that only has Shop/Look. then the shop page, it should be nothing but our product which we will list the categories ourself. And the look page should contain all the info. such as news, about us and designers etc. Thank you all for your hard work, we really enjoyed the designs. Added Monday, November 03, 2014

Target Market(s)

Our target audiences are woman aged from 16-40 who like online shopping

Industry/Entity Type

Online Shopping

Number of Pages Required

3 page

Font styles to use
Serif
Sans Serif
Script

Requirements
Must have
• Designers,
• we really like the design of helenamardoux.example(we have attached a picture of the website) , Can we get a homepage like that? so the designs you submit will be 3 pages. The first one should be a page that only has Shop/Look. then the shop page, it should be nothing but our product which we will list the categories ourself. And the look page should contain all the info. such as news, about us and designers etc. Thank you all for your hard work, we really enjoyed the designs.

```html
<!DOCTYPE html>
<html lang="en">
<head>
<meta charset="utf-8">
<title>Orbel Vantra — Home</title>
<link rel="stylesheet" href="https://fonts.googleapis.com/css2?family=Cinzel:wght@400;600&family=Crimson+Text:wght@600&display=swap">
<style>
  :root {
    --ink: #111111;
    --accent: #b0121b;
    --paper: #ffffff;
    --night: #05070d;
    --steel: #1d3a63;
    --cobalt: #3f5fa8;
    --frame: #ffffff;
  }
  * { margin: 0; padding: 0; box-sizing: border-box; }
  html, body { width: 1200px; height: 960px; overflow: hidden; background: var(--paper); }
  body { position: relative; font-family: "Crimson Text", Georgia, serif; color: var(--ink); }

  .site-header { position: absolute; left: 0; top: 0; width: 1200px; height: 113px; background: var(--paper); }
  .brand { position: absolute; left: 92px; top: 22px; width: 126px; text-align: center; }
  .brand-mark { display: block; width: 40px; height: 40px; margin: 0 auto 6px; border-radius: 50%; background: var(--accent); }
  .brand-name { display: block; font-family: "Cinzel", Georgia, serif; font-size: 11px; letter-spacing: 1.2px; line-height: 11px; color: var(--ink); }

  .main-nav { position: absolute; right: 95px; top: 46px; display: flex; align-items: center; font-size: 14.5px; letter-spacing: 0.2px; }
  .main-nav a { color: var(--ink); text-decoration: none; }
  .main-nav .sep { margin: 0 16px; }
  .main-nav .current { color: var(--accent); display: flex; align-items: center; }
  .nav-dot { display: inline-block; width: 15px; height: 15px; border-radius: 50%; background: var(--accent); margin-right: 10px; }

  .showcase { position: absolute; left: 0; top: 113px; width: 1200px; height: 847px; display: flex; }
  .look { position: relative; height: 100%; }
  .look-best { width: 601px; background: linear-gradient(160deg, #0b1424 0%, var(--steel) 35%, var(--cobalt) 60%, #141b33 100%); }
  .look-summer { width: 599px; background: linear-gradient(200deg, #0a1220 0%, var(--steel) 30%, #c9b9a6 60%, #4a6a9a 100%); }

  .look-label {
    position: absolute; top: 328px; width: 349px; height: 175px;
    border: 4px solid var(--frame);
    display: flex; flex-direction: column; justify-content: center; align-items: center;
    font-family: "Cinzel", Georgia, serif; font-weight: 600; color: var(--frame);
    font-size: 44px; line-height: 48px; letter-spacing: 0.5px; text-align: center;
  }
  .look-best .look-label { left: 125px; }
  .look-summer .look-label { left: 125px; }
</style>
</head>
<body>
  <header class="site-header">
    <div class="brand">
      <span class="brand-mark"></span>
      <span class="brand-name">ORV GROUP</span>
      <span class="brand-name">ORBEL VANTRA</span>
    </div>
    <nav class="main-nav">
      <a class="current" href="#"><span class="nav-dot"></span>HOME</a>
      <span class="sep">/</span><a href="#">ABOUT</a>
      <span class="sep">/</span><a href="#">COLLECTION</a>
      <span class="sep">/</span><a href="#">WHAT’S NEW</a>
      <span class="sep">/</span><a href="#">SHOP</a>
      <span class="sep">/</span><a href="#">CONTACT</a>
    </nav>
  </header>

  <main class="showcase">
    <section class="look look-best" role="img" aria-label="Model in a blue brushstroke-print shirt dress against a dark metallic backdrop">
      <div class="look-label"><span>BEST NEW</span><span>COLLECTION</span></div>
    </section>
    <section class="look look-summer" role="img" aria-label="Model in a white wrap dress with a colourful feather print against a dark metallic backdrop">
      <div class="look-label"><span>SUMMER</span><span>COLLECTION</span></div>
    </section>
  </main>
</body>
</html>
```